Calderwick Climate Business Card Design

Design new, 2 sides, business cards for a residential and light commercial heating, air conditioning contractor.

Target Market(s)

Homeowners, small businesses

Industry/Entity Type

Business

Contact Information for Business Card

Dominic Westerhall
Phone - 862-415-2736
Email
Address - PO box 518
Brightwater NJ 07912
Website - www.HarborBreezeLLC.example

Requirements
Must have
• logo, company colors, standard size with no die cut, so I can use nova stamp

```html
<!DOCTYPE html>
<html lang="en">
<head>
<meta charset="utf-8">
<title>Calderwick Climate Business Card</title>
<link rel="stylesheet" href="https://fonts.googleapis.com/css2?family=Montserrat:wght@400;500;700;800&display=swap">
<style>
  :root {
    --bg: #e9e9eb;
    --card: #ffffff;
    --orange: #f7941d;
    --orange-deep: #f0802a;
    --orange-light: #f9a826;
    --maroon: #9b2335;
    --ink: #1c1c1c;
    --muted: #333333;
  }
  * { box-sizing: border-box; margin: 0; padding: 0; }
  html, body { width: 1200px; height: 900px; overflow: hidden; }
  body {
    background: var(--bg);
    font-family: "Montserrat", sans-serif;
    color: var(--ink);
    position: relative;
  }
  .card {
    position: absolute;
    left: 250px;
    width: 700px;
    height: 400px;
    background: var(--card);
    border-radius: 28px;
    overflow: hidden;
    box-shadow: 0 6px 18px rgba(0,0,0,0.12);
  }
  .card--contact { top: 40px; }
  .card--brand { top: 470px; }
  .card-band {
    position: absolute;
    left: 0; bottom: 0;
    width: 100%;
    height: 44px;
  }
  .corner-mark {
    position: absolute;
    left: 40px; top: 34px;
    width: 22px; height: 22px;
    background: var(--orange);
  }
  .person {
    position: absolute;
    left: 76px; top: 30px;
  }
  .person-name {
    font-weight: 800;
    font-size: 30px;
    letter-spacing: 0.5px;
    text-transform: uppercase;
    line-height: 1;
  }
  .person-name .surname { color: var(--orange); }
  .person-role {
    margin-top: 6px;
    font-size: 15px;
    font-weight: 500;
    color: var(--muted);
  }
  .brand {
    position: absolute;
    display: flex;
    align-items: center;
    gap: 14px;
  }
  .brand-dot {
    border-radius: 50%;
    background: var(--maroon);
    flex: none;
  }
  .brand-name {
    font-weight: 800;
    color: var(--maroon);
    text-transform: uppercase;
    line-height: 1;
    white-space: nowrap;
  }
  .card--contact .brand { left: 44px; top: 126px; }
  .card--contact .brand-dot { width: 24px; height: 24px; }
  .card--contact .brand-name { font-size: 30px; }
  .card--brand .brand { left: 50%; top: 158px; transform: translateX(-50%); }
  .card--brand .brand-dot { width: 36px; height: 36px; }
  .card--brand .brand-name { font-size: 44px; }
  .contacts {
    position: absolute;
    right: 36px; bottom: 58px;
    list-style: none;
  }
  .contact-row {
    display: flex;
    align-items: center;
    justify-content: flex-end;
    gap: 14px;
    margin-top: 10px;
  }
  .contact-text {
    text-align: right;
    font-size: 15px;
    font-weight: 500;
    line-height: 1.35;
  }
  .contact-icon {
    width: 40px; height: 40px;
    flex: none;
  }
</style>
</head>
<body>

  <section class="card card--contact" aria-label="Business card, contact side">
    <div class="corner-mark"></div>
    <div class="person">
      <h1 class="person-name">Dominic <span class="surname">Westerhall</span></h1>
      <p class="person-role">CEO &amp; Founder</p>
    </div>

    <div class="brand">
      <span class="brand-dot"></span>
      <span class="brand-name">Calderwick Climate</span>
    </div>

    <ul class="contacts">
      <li class="contact-row">
        <span class="contact-text">862-555-0147</span>
        <svg class="contact-icon" viewBox="0 0 40 40" aria-hidden="true">
          <circle cx="20" cy="20" r="18" fill="none" stroke="var(--orange)" stroke-width="2"/>
          <path d="M15 12c-1 0-2.5 1.5-2.5 3 0 6 6.5 12.5 12.5 12.5 1.5 0 3-1.5 3-2.5l-3-2.5-2 1.5c-2-1-4-3-5-5l1.5-2z" fill="none" stroke="var(--orange)" stroke-width="1.8" stroke-linejoin="round"/>
        </svg>
      </li>
      <li class="contact-row">
        <span class="contact-text">info@calderwickclimate.example<br>www.CalderwickClimate.example</span>
        <svg class="contact-icon" viewBox="0 0 40 40" aria-hidden="true">
          <circle cx="20" cy="20" r="18" fill="none" stroke="var(--orange)" stroke-width="2"/>
          <circle cx="20" cy="20" r="9" fill="none" stroke="var(--orange)" stroke-width="1.6"/>
          <ellipse cx="20" cy="20" rx="4" ry="9" fill="none" stroke="var(--orange)" stroke-width="1.4"/>
          <path d="M11 20h18M12.5 15.5h15M12.5 24.5h15" stroke="var(--orange)" stroke-width="1.4"/>
        </svg>
      </li>
      <li class="contact-row">
        <span class="contact-text">PO box 518,<br>Brightwater NJ 07912</span>
        <svg class="contact-icon" viewBox="0 0 40 40" aria-hidden="true">
          <circle cx="20" cy="20" r="18" fill="none" stroke="var(--orange)" stroke-width="2"/>
          <path d="M20 29s-7-7-7-12a7 7 0 0 1 14 0c0 5-7 12-7 12z" fill="none" stroke="var(--orange)" stroke-width="1.8"/>
          <circle cx="20" cy="17" r="2.5" fill="none" stroke="var(--orange)" stroke-width="1.6"/>
        </svg>
      </li>
    </ul>

    <svg class="card-band" viewBox="0 0 700 44" preserveAspectRatio="none" aria-hidden="true">
      <rect width="700" height="44" fill="var(--orange)"/>
      <polygon points="130,0 300,0 260,44 90,44" fill="var(--orange-deep)"/>
      <polygon points="300,0 700,0 700,44 260,44" fill="var(--orange-light)" opacity="0.55"/>
    </svg>
  </section>

  <section class="card card--brand" aria-label="Business card, brand side">
    <div class="brand">
      <span class="brand-dot"></span>
      <span class="brand-name">Calderwick Climate</span>
    </div>

    <svg class="card-band" viewBox="0 0 700 44" preserveAspectRatio="none" aria-hidden="true">
      <rect width="700" height="44" fill="var(--orange)"/>
      <polygon points="200,0 380,0 340,44 160,44" fill="var(--orange-deep)"/>
      <polygon points="380,0 700,0 700,44 340,44" fill="var(--orange-light)" opacity="0.55"/>
    </svg>
  </section>

</body>
</html>
```